Vellisant - Quality health delivered at your door

Vellisant offers home and Community Based Services for adults who wish to continue live independently in their communities. We increase accessibility to health care, reduce health care delivery gap, reduce mortality and morbidity, reduce health while promoting healthy living in the comfort of our patients communities or homes.

We provide on site services and deliver high quality healthcare at your door. Our experienced physicians coordinate care with our certified nurse practitioners and provide chronic care management, physical therapy, rehabilitation and medications management.

Target Market(s)

Older population living in independent living facilities

Industry/Entity Type

Health Care

Contact Information for Business Card

Vellisant

Number of Pages Required

4 page

Font styles to use
Sans Serif

Colors

Designer to choose colors to be used in the design.

```html
<!DOCTYPE html>
<html lang="en">
<head>
<meta charset="utf-8">
<title>Vellisant – Quality health delivered at your door</title>
<link href="https://fonts.googleapis.com/css2?family=Roboto:wght@400;500;700&family=Open+Sans:wght@400;600&display=swap" rel="stylesheet">
<style>
:root{
  --green:#6e981e;
  --green-dark:#5f8619;
  --orange:#f89a00;
  --ink:#333;
  --muted:#777;
  --paper:#fff;
  --mist:#f4f5f7;
}
*{box-sizing:border-box;margin:0;padding:0}
html,body{width:1200px;height:2456px;overflow:hidden;background:var(--paper)}
body{position:relative;font-family:"Open Sans",Arial,sans-serif;color:var(--ink)}
.abs{position:absolute}
a{color:inherit;text-decoration:none}

/* header */
.top-rule{left:0;top:0;width:1200px;height:4px;background:var(--green)}
.utility-nav{top:38px;left:0;width:1200px;height:20px;font:500 12px "Roboto",sans-serif;color:#555;letter-spacing:.3px}
.utility-nav span{position:absolute;top:0}
.search-btn{left:1079px;top:30px;width:32px;height:32px;border:1.5px solid var(--orange);border-radius:50%}
.main-nav{left:0;top:90px;width:1200px;height:57px;background:var(--green)}
.main-nav span{position:absolute;top:22px;font:700 12px "Roboto",sans-serif;color:#fff;letter-spacing:.2px}
.brand-disc{left:87px;top:8px;width:180px;height:180px;border-radius:50%;background:#fff;z-index:2}
.brand-mark{left:153px;top:26px;width:48px;height:48px;border-radius:50%;background:var(--orange);z-index:3}
.brand-name{left:87px;top:106px;width:180px;text-align:center;font:500 25px "Roboto",sans-serif;color:#1d1d1d;z-index:3;letter-spacing:.5px}

/* hero */
.hero{left:0;top:147px;width:1200px;height:519px;background:linear-gradient(100deg,#5f7e35 0%,#a7b98a 35%,#dfe3d0 48%,#98ad6a 62%,#4f6d2a 100%)}
.hero-title{left:822px;top:380px;font:500 37px "Roboto",sans-serif;color:#fff}
.hero-copy{left:822px;top:436px;width:320px;font:12.5px/27px "Open Sans",sans-serif;color:#fff}
.hero-btn{left:822px;top:532px;width:123px;height:44px;border:1.5px solid #fff;color:#fff;font:500 13px/41px "Roboto",sans-serif;text-align:center}
.hero-dot{top:630px;width:16px;height:16px;border:2px solid #fff;border-radius:50%}

/* welcome */
.section-title{width:1200px;left:0;text-align:center;font:400 26px "Roboto",sans-serif;color:var(--orange)}
.welcome-copy{left:216px;top:752px;width:768px;text-align:center;font:11.5px/27px "Open Sans",sans-serif;color:var(--muted)}
.btn-green{left:529px;top:853px;width:142px;height:46px;background:var(--green);border-radius:3px;color:#fff;font:500 13px/46px "Roboto",sans-serif;text-align:center}

/* services */
.services{left:0;top:941px;width:1200px;height:491px;background:var(--mist)}
.services-sub{left:0;top:1008px;width:1200px;text-align:center;font:11.5px "Open Sans",sans-serif;color:#555}
.service{top:1056px;width:247px}
.service-photo{width:247px;height:170px}
.service-name{margin-top:24px;font:700 12.5px "Roboto",sans-serif;color:var(--orange)}
.service:nth-child(even) .service-name{color:var(--green)}
.service-copy{margin-top:14px;font:11.5px/24.5px "Open Sans",sans-serif;color:var(--muted)}
.service-link{display:inline-block;margin-top:12px;font:700 11.5px "Roboto",sans-serif;color:var(--orange);border-bottom:1px solid currentColor}
.service:nth-child(even) .service-link{color:var(--green)}

/* skilled nursing */
.feature-photo{left:0;top:1432px;width:581px;height:408px;background:linear-gradient(120deg,#e7ddd2 0%,#c9b7a6 35%,#8e8fa6 60%,#2b3352 100%)}
.feature-panel{left:581px;top:1432px;width:619px;height:408px;background:var(--orange);color:#fff}
.feature-title{left:39px;top:50px;font:500 21px "Roboto",sans-serif;letter-spacing:.3px}
.feature-copy{left:39px;top:88px;width:550px;font:11.5px/25px "Open Sans",sans-serif}
.feature-list{left:51px;top:187px;list-style:none;font:11.5px "Open Sans",sans-serif}
.feature-list li{height:39.5px;display:flex;align-items:flex-start;gap:12px}
.feature-list svg{flex:none;margin-top:2px}

/* testimonial */
.quote-mark{font:700 30px "Roboto",serif;color:#c9c9c9}
.quote-copy{left:177px;top:1944px;width:540px;font:11.5px/22.5px "Open Sans",sans-serif;color:#555}
.quote-name{left:177px;top:2061px;font:700 13px "Roboto",sans-serif;color:var(--green)}
.quote-date{left:177px;top:2084px;font:11.5px "Open Sans",sans-serif;color:var(--muted)}
.avatar{left:772px;top:1910px;width:200px;height:200px;border-radius:50%;border:5px solid #eee;background:radial-gradient(circle at 50% 40%,#c79a80,#6a4a3a)}

/* footer */
.footer{left:0;top:2154px;width:1200px;height:231px;background:var(--green);color:#fff}
.footer-mark{left:174px;top:26px;width:120px;height:120px;border-radius:50%;background:var(--orange);border:5px solid #1d1d1d}
.footer-name{left:84px;top:152px;width:300px;text-align:center;font:500 38px "Roboto",sans-serif;color:#1d1d1d;letter-spacing:.5px}
.footer-heading{top:36px;font:700 17px "Roboto",sans-serif;letter-spacing:.5px}
.contact-list{left:403px;top:84px;list-style:none;font:11.5px "Open Sans",sans-serif}
.contact-list li{display:flex;gap:12px;height:29.5px;align-items:flex-start}
.contact-list li.email span{text-decoration:underline}
.contact-list svg{flex:none;margin-top:1px}
.news-copy{left:625px;top:78px;width:200px;font:11.5px/20px "Open Sans",sans-serif}
.news-input{left:625px;top:133px;width:230px;height:33px;background:#fff;color:#666;font:11.5px/33px "Open Sans",sans-serif;padding-left:14px}
.news-btn{left:625px;top:176px;width:82px;height:24px;background:var(--orange);font:600 10px/24px "Open Sans",sans-serif;text-align:center}
.follow-copy{left:912px;top:80px;width:215px;font:11.5px/19px "Open Sans",sans-serif}
.social{top:154px;width:36px;height:36px;border:1.5px solid #fff;border-radius:50%}
.legal{left:0;top:2385px;width:1200px;height:71px;background:var(--green-dark);color:#fff;text-align:center;font:11.5px/66px "Open Sans",sans-serif}
</style>
</head>
<body>

<div class="abs top-rule"></div>
<nav class="abs utility-nav">
  <span style="left:532px">RESPITE CARE</span>
  <span style="left:647px">REHABILITATION</span>
  <span style="left:778px">MEMORA LEARNING CENTER</span>
  <span style="left:963px">MEMORA LEARNING</span>
</nav>
<div class="abs search-btn">
  <svg width="29" height="29" viewBox="0 0 29 29"><circle cx="13.5" cy="13.5" r="4" fill="none" stroke="#f89a00" stroke-width="1.6"/><line x1="16.5" y1="16.5" x2="19.5" y2="19.5" stroke="#f89a00" stroke-width="1.8"/></svg>
</div>
<nav class="abs main-nav">
  <span style="left:295px">HOME</span>
  <span style="left:386px">ASSISTED LIVING</span>
  <span style="left:539px">SKILLED NURSING</span>
  <span style="left:694px">INDEPENDENT LIVING</span>
  <span style="left:873px">HOME &amp; COMMUNITY BASED SERVICES</span>
</nav>
<div class="abs brand-disc"></div>
<div class="abs brand-mark"></div>
<div class="abs brand-name">VELLISANT</div>

<section>
  <div class="abs hero" role="img" aria-label="Older couple walking arm in arm along a tree-lined park path"></div>
  <h1 class="abs hero-title">Vellisant</h1>
  <p class="abs hero-copy">Vellisant offers home and Community Based Services for adults who wish to continue to live independently in the and deliver high quality healthcare at your door.</p>
  <a class="abs hero-btn">READ MORE</a>
  <span class="abs hero-dot" style="left:85px"></span>
  <span class="abs hero-dot" style="left:128px"></span>
</section>

<section>
  <h2 class="abs section-title" style="top:703px">Welcome to Vellisant</h2>
  <p class="abs welcome-copy">Vellisant offers home and Community Based Services for adults who wish to continue to live independently in the comfort of their communities. We provide on site services and deliver high quality healthcare at your door. Our experienced physicians coordinate care with our certified and provide chronic care management, physical therapy, rehabilitation and medications management.</p>
  <a class="abs btn-green">READ MORE INFO</a>
</section>

<section>
  <div class="abs services"></div>
  <h2 class="abs section-title" style="top:966px">Our Services</h2>
  <p class="abs services-sub">Sed ut perspiciatis unde omnis iste natus error sit voluptatem accusantium doloremque laudantium, totam rem aperiam</p>
  <div>
    <article class="abs service" style="left:87px">
      <div class="service-photo" role="img" aria-label="Caregiver hugging a smiling older woman at home" style="background:linear-gradient(135deg,#f1e4d8,#9fb7d6)"></div>
      <h3 class="service-name">HOME HEALTH ASSISTANCE</h3>
      <p class="service-copy">Sed ut perspiciatis unde omnis iste natus err or sit voluptatem accusantium doloremquete to beatae vitae dicta sunt explicabo.</p>
      <a class="service-link">READ MORE</a>
    </article>
    <article class="abs service" style="left:347px">
      <div class="service-photo" role="img" aria-label="Therapist guiding a patient through floor exercises on a mat" style="background:linear-gradient(135deg,#e9dccb,#b9a98f 55%,#3f6c6a)"></div>
      <h3 class="service-name">PHYSICAL THERAPY</h3>
      <p class="service-copy">Sed ut perspiciatis unde omnis iste natus err or sit voluptatem accusantium doloremquete to beatae vitae dicta sunt explicabo.</p>
      <a class="service-link">READ MORE</a>
    </article>
    <article class="abs service" style="left:607px">
      <div class="service-photo" role="img" aria-label="Nurse in blue scrubs talking with an older patient" style="background:linear-gradient(135deg,#eef1f4,#4a86c6 55%,#e9e6e0)"></div>
      <h3 class="service-name">MENTAL HEALTH</h3>
      <p class="service-copy">Sed ut perspiciatis unde omnis iste natus err or sit voluptatem accusantium doloremquete to beatae vitae dicta sunt explicabo.</p>
      <a class="service-link">READ MORE</a>
    </article>
    <article class="abs service" style="left:866px">
      <div class="service-photo" role="img" aria-label="Older woman brushing her teeth" style="background:linear-gradient(135deg,#c9b8a8,#7c6a5e 55%,#2f3d6a)"></div>
      <h3 class="service-name">DENTAL HEALTH</h3>
      <p class="service-copy">Sed ut perspiciatis unde omnis iste natus err or sit voluptatem accusantium doloremquete to beatae vitae dicta sunt explicabo.</p>
      <a class="service-link">READ MORE</a>
    </article>
  </div>
</section>

<section>
  <div class="abs feature-photo" role="img" aria-label="Smiling nurse embracing an older man holding a walking cane"></div>
  <div class="abs feature-panel">
    <h2 class="abs feature-title">SKILLED NURSING</h2>
    <p class="abs feature-copy">Sed ut perspiciatis unde omnis iste natus error sit voluptatem accusantium doloremque laudantium, totam rem aperiam, eaque ipsa quae ab illo inventore veritatis et quasi arc Nieaque ipsa quae ab illo beatae vitae dicta sunt explicabo.</p>
    <ul class="abs feature-list">
      <li><svg width="10" height="10" viewBox="0 0 10 10"><path d="M1 5.5 4 8.5 9 1.5" fill="none" stroke="#fff" stroke-width="1.8"/></svg>Sed ut perspiciatis unde omnis iste natus</li>
      <li><svg width="10" height="10" viewBox="0 0 10 10"><path d="M1 5.5 4 8.5 9 1.5" fill="none" stroke="#fff" stroke-width="1.8"/></svg>Error sit voluptatem accusantium doloremque</li>
      <li><svg width="10" height="10" viewBox="0 0 10 10"><path d="M1 5.5 4 8.5 9 1.5" fill="none" stroke="#fff" stroke-width="1.8"/></svg>Laudantium, totam rem aperiam, eaque ipsa</li>
      <li><svg width="10" height="10" viewBox="0 0 10 10"><path d="M1 5.5 4 8.5 9 1.5" fill="none" stroke="#fff" stroke-width="1.8"/></svg>Quae ab illo inventore veritatis et quasi arc</li>
      <li><svg width="10" height="10" viewBox="0 0 10 10"><path d="M1 5.5 4 8.5 9 1.5" fill="none" stroke="#fff" stroke-width="1.8"/></svg>Quae ab illo beatae vitae dicta sunt explicabo.</li>
    </ul>
  </div>
</section>

<section>
  <span class="abs quote-mark" style="left:158px;top:1912px">“</span>
  <p class="abs quote-copy">Sed ut perspiciatis unde omnis iste natus error sit voluptatem accusantium doloremque laudantium, totam rem aperiam, eaque ipsa quae ab illo inventore veritatis et quasi architecto beatae vitae dicta sunt explicabo. Nemo enim ipsam voluptatem quia voluptas sit aspernatur aut odit aut fugit, sed quia consequuntur magni dolores eos qui ratione voluptatem sequi nesciunt.</p>
  <span class="abs quote-mark" style="left:560px;top:2020px">”</span>
  <p class="abs quote-name">MARA ELLISON</p>
  <p class="abs quote-date">Posted On 07 July 2017</p>
  <div class="abs avatar" role="img" aria-label="Portrait of the client giving the testimonial"></div>
</section>

<footer>
  <div class="abs footer">
    <div class="abs footer-mark"></div>
    <div class="abs footer-name">VELLISANT</div>

    <h4 class="abs footer-heading" style="left:403px">CONTACT US</h4>
    <ul class="abs contact-list">
      <li><svg width="13" height="13" viewBox="0 0 13 13"><path d="M2 5C2 3 4 2 6.5 2S11 3 11 5H9V4H4V5ZM3 6H10L11 11H2Z" fill="#fff"/></svg><span>(000)-555-0142 (Phone)</span></li>
      <li><svg width="13" height="13" viewBox="0 0 13 13"><rect x="3" y="1" width="7" height="4" fill="#fff"/><rect x="1" y="5" width="11" height="5" fill="#fff"/><rect x="3" y="8" width="7" height="4" fill="#fff" stroke="#6e981e"/></svg><span>(000)-555-0142 &nbsp;(Fax)</span></li>
      <li class="email"><svg width="13" height="13" viewBox="0 0 13 13"><rect x="1" y="3" width="11" height="8" fill="#fff"/><path d="M1 3 6.5 7.5 12 3" fill="none" stroke="#6e981e"/></svg><span>info@vellisant.com</span></li>
      <li><svg width="13" height="13" viewBox="0 0 13 13"><path d="M6.5 1C4.3 1 3 2.6 3 4.5 3 7 6.5 12 6.5 12S10 7 10 4.5C10 2.6 8.7 1 6.5 1Z" fill="#fff"/><circle cx="6.5" cy="4.5" r="1.3" fill="#6e981e"/></svg><span>#124 lorem Ipsum dummy<br>Text Lorem</span></li>
    </ul>

    <h4 class="abs footer-heading" style="left:625px">NEWSLETTER</h4>
    <p class="abs news-copy">Register Your email address to get information ablout us</p>
    <div class="abs news-input">Email Address</div>
    <div class="abs news-btn">SUBSCRIBE</div>

    <h4 class="abs footer-heading" style="left:912px">FOLLOW US</h4>
    <p class="abs follow-copy">Lorem ipsum dolor sit amet, conse ctetur adipiscing elit. Nulla in purus nibh. Donec ornare</p>
    <span class="abs social" style="left:909px"></span>
    <span class="abs social" style="left:953px"></span>
    <span class="abs social" style="left:997px"></span>
    <span class="abs social" style="left:1041px"></span>
    <span class="abs social" style="left:1079px"></span>
  </div>
  <div class="abs legal">© Copyright 2017 Vellisant.All Rights Reserved</div>
</footer>

</body>
</html>
```